Upgrade/"Tweak" My Landing Page

We need to "tweak" our current landing page. I'm a perfectionist and something seems "off". Things I LOVE about our current page: I love our message that "ONE SIZE DOES NOT FIT ALL", as well as the photo used (boy wearing an oversized hat). I also like the fact that the photo is in full screen mode- I like this look.
THINGS I DON'T Like: The font & location of our message "ONE SIZE DOES NOT FIT ALL" - just seems "off". I'm also concerned about the placement of our menu being on the left hand side of the screen. Not sure if this is ideal. Also, my product types are listed on the left hand side of the screen in the menu section. My audience seems to think these are links when in fact they are just examples of the products I sell. How can I position these so the audience knows it's for informational purposes only.
Help!! I want my landing page to be PERFECT.

```html
<!DOCTYPE html>
<html lang="en">
<head>
<meta charset="utf-8">
<title>Meridian Insurance Agency</title>
<link rel="stylesheet" href="https://fonts.googleapis.com/css2?family=Oswald:wght@300;400&family=Roboto:wght@300;400;500;700&family=Open+Sans:wght@600&display=swap">
<style>
  :root {
    --navy: #1c2f63;
    --nav-blue: #41608f;
    --band-blue: #42608f;
    --sky-top: #6f9fd9;
    --sky-bottom: #a8c2e3;
    --red: #e8304a;
    --pink: #f06a7c;
    --grey-icon: #8c8c8c;
    --grey-line: #dedede;
    --grey-band: #f5f5f5;
    --grey-text: #8a8a8a;
    --ink: #13234a;
    --white: #ffffff;
  }
  * { margin: 0; padding: 0; box-sizing: border-box; }
  html, body { width: 1200px; height: 1000px; overflow: hidden; background: var(--white); }
  .page { position: relative; width: 1200px; height: 1000px; font-family: "Roboto", Arial, sans-serif; }

  .site-header { position: absolute; top: 0; left: 0; width: 1200px; height: 110px; display: flex; align-items: center; justify-content: center; gap: 12px; }
  .brand-mark { width: 14px; height: 14px; background: var(--navy); }
  .brand-name { font-weight: 700; color: var(--navy); font-size: 15px; line-height: 20px; text-align: center; letter-spacing: 0.5px; }

  .main-nav { position: absolute; top: 110px; left: 0; width: 1200px; height: 39px; background: var(--nav-blue); display: flex; align-items: center; justify-content: center; font-family: "Open Sans", Arial, sans-serif; font-weight: 600; font-size: 11px; color: var(--white); }
  .main-nav span.sep { margin: 0 16px; }

  .hero { position: absolute; top: 149px; left: 0; width: 1200px; height: 414px; overflow: hidden; }
  .hero-photo { position: absolute; inset: 0; background: linear-gradient(180deg, var(--sky-top), var(--sky-bottom)); }
  .hero-contact { position: absolute; top: 16px; left: 696px; display: flex; align-items: center; gap: 4px; font-size: 14px; color: var(--ink); }
  .hero-contact .slash { color: rgba(255,255,255,0.8); margin: 0 3px; }
  .social { display: flex; gap: 4px; margin-left: 8px; }
  .social span { width: 17px; height: 17px; background: var(--nav-blue); display: block; }
  .social span + span { background: #2f86c4; }
  .hero-copy { position: absolute; top: 272px; left: 0; width: 1200px; text-align: center; color: var(--white); }
  .hero-title { font-family: "Oswald", "Arial Narrow", sans-serif; font-weight: 400; font-size: 55px; line-height: 64px; transform: scaleX(0.745); }
  .hero-sub { font-weight: 700; font-size: 21.5px; line-height: 24px; margin-top: -2px; }
  .hero-button { display: inline-block; margin-top: 14px; width: 107px; height: 26px; border: 1.5px solid var(--white); font-size: 14px; line-height: 23px; letter-spacing: 0.3px; }

  .products-heading { position: absolute; top: 563px; left: 0; width: 1200px; height: 80px; background: var(--grey-band); border-bottom: 1px solid var(--grey-line); text-align: center; font-weight: 300; font-size: 21.5px; line-height: 84px; color: var(--grey-text); }
  .product-list { position: absolute; top: 643px; left: 0; width: 1200px; height: 119px; }
  .product { position: absolute; top: 24px; height: 77px; text-align: center; }
  .product + .product { border-left: 1px solid var(--grey-line); }
  .product-name { font-weight: 500; font-size: 10.5px; line-height: 10px; color: var(--red); padding-top: 2px; }
  .product svg { position: absolute; left: 50%; top: 44px; transform: translateX(-50%); fill: var(--grey-icon); }

  .contact-band { position: absolute; top: 762px; left: 0; width: 1200px; height: 168px; background: var(--band-blue); }
  .city-photo { position: absolute; left: 175px; top: 0; width: 850px; height: 168px; background: linear-gradient(90deg, rgba(66,96,143,1), rgba(50,70,110,0.6) 12%, rgba(40,58,95,0.65) 50%, rgba(50,70,110,0.6) 88%, rgba(66,96,143,1)); }
  .contact-copy { position: absolute; top: 43px; left: 0; width: 1200px; text-align: center; color: var(--white); font-weight: 300; font-size: 16px; line-height: 23px; }
  .contact-phones { position: absolute; top: 101px; left: 0; width: 1200px; display: flex; justify-content: center; align-items: center; gap: 10px; font-size: 21px; color: var(--pink); }
  .contact-phones .slash { color: var(--white); }

  .site-footer { position: absolute; top: 930px; left: 0; width: 1200px; height: 70px; text-align: center; }
  .footer-links { margin-top: 24px; font-size: 8.8px; color: var(--ink); }
  .copyright { margin-top: 4px; font-size: 8.5px; color: #777; }
</style>
</head>
<body>
<div class="page">
  <header class="site-header">
    <span class="brand-mark"></span>
    <div class="brand-name">MERIDIAN INSURANCE<br>AGENCY</div>
  </header>

  <nav class="main-nav">
    <span>About us</span><span class="sep">|</span>
    <span>Pay your bill</span><span class="sep">|</span>
    <span>Request a quote or policy change</span><span class="sep">|</span>
    <span>File a claim</span><span class="sep">|</span>
    <span>Contact us</span>
  </nav>

  <section class="hero">
    <div class="hero-photo" role="img" aria-label="Full-width photo of a child in an oversized red sun hat against a blue sky"></div>
    <div class="hero-contact">
      <svg width="16" height="16" viewBox="0 0 16 16" aria-hidden="true"><circle cx="8" cy="8" r="7" fill="none" stroke="#fff" stroke-width="1.3"/><path d="M5.3 4.5c.4-.3.8-.2 1 .2l.6 1.2c.2.4 0 .7-.3.9l-.3.3c.3.8 1 1.5 1.8 1.9l.3-.3c.3-.3.6-.4.9-.2l1.2.6c.4.2.5.6.2 1-.6.9-1.4 1.1-2.3.7-1.6-.7-2.8-1.9-3.5-3.5-.3-.9-.2-1.8.4-2.8z" fill="#fff"/></svg>
      <span>877.555.0142</span><span class="slash">/</span><span>281.555.0176</span>
      <div class="social"><span></span><span></span></div>
    </div>
    <div class="hero-copy">
      <h1 class="hero-title">ONE SIZE DOES NOT FIT ALL</h1>
      <p class="hero-sub">Custom-made solutions at your fingertips</p>
      <span class="hero-button">KNOW MORE</span>
    </div>
  </section>

  <h2 class="products-heading">Our Insurance Products</h2>
  <div class="product-list">
    <div class="product" style="left:240px;width:64px"><p class="product-name">HOME</p>
      <svg width="26" height="22" viewBox="0 0 26 22"><path d="M13 1L1 11h3v10h7v-6h4v6h7V11h3z"/></svg></div>
    <div class="product" style="left:304px;width:67px"><p class="product-name">CONDO</p>
      <svg width="20" height="30" viewBox="0 0 20 30"><path d="M1 0h18v30h-7v-5H8v5H1z"/><g fill="#fff"><rect x="4" y="4" width="4" height="4"/><rect x="12" y="4" width="4" height="4"/><rect x="4" y="11" width="4" height="4"/><rect x="12" y="11" width="4" height="4"/><rect x="4" y="18" width="4" height="4"/><rect x="12" y="18" width="4" height="4"/></g></svg></div>
    <div class="product" style="left:371px;width:78px"><p class="product-name">BUSINESS</p>
      <svg width="22" height="20" viewBox="0 0 22 20"><path d="M7 1h8v4h-2V3H9v2H7z"/><rect x="1" y="5" width="20" height="14" rx="2"/><g fill="#fff"><rect x="6" y="8" width="1.5" height="9"/><rect x="14.5" y="8" width="1.5" height="9"/></g></svg></div>
    <div class="product" style="left:449px;width:94px"><p class="product-name">WINDSTORM</p>
      <svg width="30" height="26" viewBox="0 0 30 26"><path d="M7 16a5 5 0 010-10 7 7 0 0113 0 5 5 0 010 10z"/><path d="M4 20h16M8 23h16M12 17h14" stroke="#8c8c8c" stroke-width="1.3" fill="none"/></svg></div>
    <div class="product" style="left:543px;width:60px"><p class="product-name">FLOOD</p>
      <svg width="26" height="26" viewBox="0 0 26 26"><path d="M13 1L4 9h2v7h14V9h2z"/><rect x="11" y="10" width="4" height="4" fill="#fff"/><path d="M2 19c3-2 5 2 8 0s5 2 8 0 5 2 6 0M2 23c3-2 5 2 8 0s5 2 8 0 5 2 6 0" stroke="#8c8c8c" stroke-width="1.6" fill="none"/></svg></div>
    <div class="product" style="left:603px;width:54px"><p class="product-name">CAR</p>
      <svg width="28" height="20" viewBox="0 0 28 20"><path d="M6 3h16l4 7v7h-3v2h-4v-2H9v2H5v-2H2v-7z"/><path d="M8 5h12l2.5 5h-17z" fill="#fff"/><circle cx="7" cy="13" r="2" fill="#fff"/><circle cx="21" cy="13" r="2" fill="#fff"/></svg></div>
    <div class="product" style="left:657px;width:60px"><p class="product-name">BOAT</p>
      <svg width="26" height="26" viewBox="0 0 26 26"><path d="M12 1v17H3zM14 4l8 14h-8z"/><path d="M1 20h24l-3 5H4z"/></svg></div>
    <div class="product" style="left:717px;width:102px"><p class="product-name">MOTORCYCLE</p>
      <svg width="36" height="22" viewBox="0 0 36 22"><circle cx="7" cy="15" r="6" fill="none" stroke="#8c8c8c" stroke-width="2"/><circle cx="29" cy="15" r="6" fill="none" stroke="#8c8c8c" stroke-width="2"/><path d="M9 9l5-3h9l3 3-4 6h-7z"/><path d="M22 3h5l3 11" stroke="#8c8c8c" stroke-width="2" fill="none"/></svg></div>
    <div class="product" style="left:819px;width:144px"><p class="product-name">PERSONAL UMBRELLA<br>POLICY</p>
      <svg width="26" height="26" viewBox="0 0 26 26"><path d="M13 2C6 2 1 7 1 12c2-2 4-2 6 0 2-2 4-2 6 0 2-2 4-2 6 0 2-2 4-2 6 0 0-5-5-10-12-10z"/><path d="M13 12v10c0 2-3 2-3 0" stroke="#8c8c8c" stroke-width="1.6" fill="none"/></svg></div>
  </div>

  <section class="contact-band">
    <div class="city-photo" role="img" aria-label="Photo of a dense city skyline seen from above, tinted blue"></div>
    <p class="contact-copy">If you are looking for a team that is highly experienced and knowledgeable, and<br>one who will be honest with you about your insurance needs, let's talk!</p>
    <div class="contact-phones">
      <svg width="20" height="20" viewBox="0 0 16 16" aria-hidden="true"><circle cx="8" cy="8" r="7" fill="none" stroke="#fff" stroke-width="1.2"/><path d="M5.3 4.5c.4-.3.8-.2 1 .2l.6 1.2c.2.4 0 .7-.3.9l-.3.3c.3.8 1 1.5 1.8 1.9l.3-.3c.3-.3.6-.4.9-.2l1.2.6c.4.2.5.6.2 1-.6.9-1.4 1.1-2.3.7-1.6-.7-2.8-1.9-3.5-3.5-.3-.9-.2-1.8.4-2.8z" fill="#fff"/></svg>
      <span>877.555.0142</span><span class="slash">/</span><span>281.555.0176</span>
    </div>
  </section>

  <footer class="site-footer">
    <p class="footer-links">Home / About us / Pay your bill / Request a quote or policy change / File a claim / Contact us</p>
    <p class="copyright">© Meridian Insurance Agency, 2015. All rights reserved.</p>
  </footer>
</div>
</body>
</html>
```